Real Estate Business Card

On the front side I want to have my info, my brokerage info.
On the back side I want have my complany’s logo, website and Facebook link. I will provide all this once I select a design.

I would like to see Black background and gold text, Dark Blue and gold text and White and blue text designs

Font styles to use
Sans Serif
Script

```html
<!DOCTYPE html>
<html lang="en">
<head>
<meta charset="UTF-8">
<title>Northgate Realty – Business Card</title>
<link href="https://fonts.googleapis.com/css2?family=Oswald:wght@500&family=Work+Sans:wght@400;500;700;800&display=swap" rel="stylesheet">
<style>
  :root {
    --brand-blue: #1c3f8a;
    --brand-navy: #0f2347;
    --brand-navy-deep: #0a1830;
    --gold: #c9a24a;
    --gold-light: #dcbd6f;
    --ink: #3a3f4a;
    --card-white: #ffffff;
    --backdrop: #2b2b2d;
  }
  * { margin: 0; padding: 0; box-sizing: border-box; }
  html, body { width: 1200px; height: 900px; overflow: hidden; }
  body {
    background: var(--backdrop);
    font-family: "Work Sans", Arial, sans-serif;
    position: relative;
  }
  .card {
    position: absolute;
    left: 250px;
    width: 700px;
    height: 400px;
    border-radius: 4px;
    box-shadow: 0 10px 30px rgba(0,0,0,.45);
    overflow: hidden;
  }
  .card-front { top: 30px; background: linear-gradient(135deg, #ffffff 55%, #eef0f4); }
  .card-back {
    top: 470px;
    background: radial-gradient(circle at 40% 40%, var(--brand-navy), var(--brand-navy-deep));
  }

  /* Front */
  .identity {
    position: absolute; left: 60px; top: 118px; width: 280px; text-align: right;
  }
  .agent-name {
    font-family: "Oswald", "Arial Narrow", sans-serif;
    font-weight: 500; font-size: 44px; color: var(--brand-blue);
    text-transform: uppercase; letter-spacing: .5px; line-height: 1;
  }
  .agent-title { font-size: 17px; color: var(--ink); margin-top: 6px; }

  .divider {
    position: absolute; left: 362px; top: 116px; width: 2px; height: 76px;
    background: var(--brand-blue);
  }

  .contact { position: absolute; left: 385px; top: 114px; list-style: none; }
  .contact li {
    display: flex; align-items: center; gap: 10px;
    font-size: 17px; color: var(--ink); line-height: 26px;
  }
  .contact svg { width: 13px; height: 13px; flex: none; }
  .contact .accent { color: var(--brand-blue); }

  .address {
    position: absolute; left: 70px; top: 268px;
    font-size: 16px; font-style: normal; color: var(--ink); line-height: 24px;
  }

  .brokerage {
    position: absolute; left: 360px; top: 300px;
    display: flex; align-items: center; gap: 22px;
  }
  .brokerage-name {
    font-weight: 800; font-size: 22px; color: var(--brand-blue); letter-spacing: .5px;
  }
  .award-badge {
    width: 36px; height: 36px; border-radius: 50%; background: var(--brand-blue);
  }

  /* Back */
  .brand-lockup {
    position: absolute; left: 0; right: 0; top: 120px;
    display: flex; align-items: center; justify-content: center; gap: 22px;
  }
  .brand-square { width: 64px; height: 64px; background: var(--gold); }
  .brand-name {
    font-weight: 800; font-size: 48px; color: var(--gold);
    letter-spacing: 2px; text-transform: uppercase; line-height: 1.05;
  }
  .back-links {
    position: absolute; left: 0; right: 0; bottom: 48px;
    display: flex; justify-content: center; gap: 40px; list-style: none;
  }
  .back-links li {
    font-size: 17px; font-weight: 500; color: var(--gold-light); letter-spacing: .3px;
  }
  .back-rule {
    position: absolute; left: 200px; right: 200px; bottom: 94px;
    height: 1px; background: var(--gold); opacity: .6;
  }
</style>
</head>
<body>

<section class="card card-front">
  <div class="identity">
    <h1 class="agent-name">Daniel Hart</h1>
    <p class="agent-title">Director</p>
  </div>
  <div class="divider"></div>
  <ul class="contact">
    <li>
      <svg viewBox="0 0 16 16"><path d="M4 1l3 3-2 2c1 2 3 4 5 5l2-2 3 3-2 3C7 15 1 9 1 3z" fill="#1c3f8a"/></svg>
      +1 555-014-2290
    </li>
    <li>
      <svg viewBox="0 0 16 16"><rect x="1" y="3" width="14" height="10" fill="none" stroke="#1c3f8a" stroke-width="2"/><path d="M1 3l7 6 7-6" fill="none" stroke="#1c3f8a" stroke-width="2"/></svg>
      hello@northgaterealty.com
    </li>
    <li>
      <svg viewBox="0 0 16 16"><circle cx="8" cy="8" r="7" fill="none" stroke="#1c3f8a" stroke-width="2"/><path d="M1 8h14M8 1c-4 4-4 10 0 14M8 1c4 4 4 10 0 14" fill="none" stroke="#1c3f8a" stroke-width="1.4"/></svg>
      <span>www.<span class="accent">northgaterealty</span>.com</span>
    </li>
  </ul>
  <address class="address">
    1180 Cedar Ave #310<br>
    Brookfield, Ontario K1A 4B2
  </address>
  <div class="brokerage">
    <span class="brokerage-name">Summit Brokers</span>
    <div class="award-badge" role="img" aria-label="Brokerage award badge"></div>
  </div>
</section>

<section class="card card-back">
  <div class="brand-lockup">
    <div class="brand-square"></div>
    <div class="brand-name">Northgate<br>Realty</div>
  </div>
  <div class="back-rule"></div>
  <ul class="back-links">
    <li>www.northgaterealty.com</li>
    <li>facebook.com/northgaterealty</li>
  </ul>
</section>

</body>
</html>
```